Letterhead Creation

I would like to create a letterhead incorporating my family crest attached. My current letterhead with my information is also attached. I would also like to add my Paralegal Rosalind Pembry

```html
<!DOCTYPE html>
<html lang="en">
<head>
<meta charset="utf-8">
<title>Letterhead – Law Offices of Martin R. Hale</title>
<link rel="stylesheet" href="https://fonts.googleapis.com/css2?family=Questrial&family=Mulish:ital,wght@1,700&display=swap">
<style>
  :root {
    --backdrop: #e4e4e4;
    --paper: #f6f6f6;
    --navy-deep: #1a2d5e;
    --navy: #22407f;
    --royal: #3159a8;
    --slate: #1f3245;
    --watermark: #d9d6d2;
    --ink-light: #ffffff;
  }
  * { margin: 0; padding: 0; box-sizing: border-box; }
  html, body {
    width: 1200px; height: 1000px; overflow: hidden;
    background: var(--backdrop);
    font-family: "Questrial", "Century Gothic", sans-serif;
  }
  .letterhead {
    position: absolute; left: 300px; top: 112px;
    width: 600px; height: 776px;
    background: var(--paper);
    box-shadow: 0 18px 40px rgba(0,0,0,0.18);
    overflow: hidden;
  }
  .masthead { position: absolute; left: 22px; top: 14px; width: 370px; height: 80px; }
  .masthead__seal {
    position: absolute; left: 0; top: 0;
    width: 66px; height: 66px; border-radius: 50%;
    background: var(--navy);
  }
  .masthead__banner {
    position: absolute; left: 4px; top: 30px;
    width: 350px; height: 28px;
    background: linear-gradient(90deg, var(--royal), var(--navy) 60%, var(--slate));
    clip-path: polygon(5% 0, 100% 0, 95% 100%, 0 100%);
  }
  .masthead__name {
    position: absolute; left: 90px; top: 37px;
    color: var(--ink-light); font-size: 13px; line-height: 14px; letter-spacing: 0.4px;
    white-space: nowrap;
  }
  .watermark {
    position: absolute; left: 50%; top: 250px; transform: translateX(-50%);
    display: flex; flex-direction: column; align-items: center; gap: 16px;
  }
  .watermark__seal { width: 150px; height: 150px; border-radius: 50%; background: var(--watermark); }
  .watermark__name { color: var(--watermark); font-size: 26px; letter-spacing: 2px; white-space: nowrap; }
  .footer-wave { position: absolute; left: 0; bottom: 0; width: 600px; height: 200px; display: block; }
  .contact {
    position: absolute; right: 24px; bottom: 24px; width: 200px;
    color: var(--ink-light); font-size: 10.5px; text-align: right;
    font-style: normal;
  }
  .contact__row {
    display: flex; justify-content: flex-end; align-items: center; gap: 10px;
    padding: 4px 0; border-bottom: 1px solid rgba(255,255,255,0.25);
  }
  .contact__row--address { line-height: 1.25; }
  .contact__row svg { width: 11px; height: 11px; flex: none; fill: var(--ink-light); }
  .contact__paralegal {
    margin-top: 7px; padding-right: 2px;
    font-family: "Mulish", "Century Gothic", sans-serif;
    font-style: italic; font-weight: 700; font-size: 10.5px;
  }
</style>
</head>
<body>
  <main class="letterhead">
    <header class="masthead">
      <div class="masthead__banner"></div>
      <div class="masthead__seal"></div>
      <span class="masthead__name">LAW OFFICES OF MARTIN R. HALE</span>
    </header>

    <div class="watermark" aria-hidden="true">
      <div class="watermark__seal"></div>
      <span class="watermark__name">MARTIN R. HALE</span>
    </div>

    <svg class="footer-wave" viewBox="0 0 600 200" preserveAspectRatio="none" aria-hidden="true">
      <defs>
        <linearGradient id="waveFill" x1="0" y1="0" x2="1" y2="0">
          <stop offset="0" stop-color="#22407f"/>
          <stop offset="0.5" stop-color="#3159a8"/>
          <stop offset="1" stop-color="#1f3245"/>
        </linearGradient>
      </defs>
      <path d="M0,52 Q270,125 600,0 L600,200 L0,200 Z" fill="url(#waveFill)"/>
      <path d="M0,52 Q150,72 260,110 Q330,140 400,200 L0,200 Z" fill="#1a2d5e"/>
      <path d="M0,80 Q170,100 290,150 Q330,170 360,200 L0,200 Z" fill="#1d3570"/>
    </svg>

    <address class="contact">
      <div class="contact__row">(555)0142873
        <svg viewBox="0 0 24 24"><path d="M6.6 10.8a15 15 0 0 0 6.6 6.6l2.2-2.2a1 1 0 0 1 1-.25 11.4 11.4 0 0 0 3.6.57 1 1 0 0 1 1 1V20a1 1 0 0 1-1 1A17 17 0 0 1 3 4a1 1 0 0 1 1-1h3.5a1 1 0 0 1 1 1c0 1.25.2 2.450.57 3.6a1 1 0 0 1-.25 1z"/></svg>
      </div>
      <div class="contact__row">(555)0197361
        <svg viewBox="0 0 24 24"><path d="M6 3h9v5H6z M3 9h18v12H3z M6 12h3v2H6z M11 12h3v2h-3z M6 16h3v2H6z M11 16h3v2h-3z M16 12h3v6h-3z"/></svg>
      </div>
      <div class="contact__row">martin@halelawpc.com
        <svg viewBox="0 0 24 24"><path d="M2 5h20v14H2z M4 7v.5l8 5 8-5V7z" fill-rule="evenodd"/></svg>
      </div>
      <div class="contact__row contact__row--address"><span>Linden, Ca 90210<br>412 N. Orchard Ave.</span>
        <svg viewBox="0 0 24 24"><path d="M12 2a7 7 0 0 0-7 7c0 5 7 13 7 13s7-8 7-13a7 7 0 0 0-7-7zm0 9.5A2.5 2.5 0 1 1 12 6.5a2.5 2.5 0 0 1 0 5z"/></svg>
      </div>
      <p class="contact__paralegal">Paralegal: Rosalind Pembry</p>
    </address>
  </main>
</body>
</html>
```